New Fresh design for online Rabbit Game

Hi,

we are a french company working on a online rabbits game for kids, and not kids.

Our website is www.zorvelo.fr, but you can look at the US version : www.quintamble.com

We buy our actual design 2 years ago, but we now think it's too boring and washed out...

We need yours talent to make a really more exacting, more colorful, fresh and dynamic design.

In our game, players have to breed and train rabbits and to make them run races. Players run again friends or players.

Players are kids, between 8 and 15 years. But best players are often parents of these kids !

Our ambiance is clearly funny. We really like if color theme or background look like a nice blue sky, and / or beach. Something that make people happy to come, and say "You are here on holly days to have fun !"

I think the best is if we have 2 layouts, one for the Home page, and one for all other page.

For home page, we are really open to any proposition, we just need to keep our features :
- registration (with rabbit preview)
- connection
- game preview (images slide with small text)
- live race preview (as we have actually)

For other pages layout, we need a layout with a standard container (maybe 850 px width?), and our 2 navigation's bar.

We only need psd, no html integration.

Thanks for your help, please ask me for any questions.
Updates

Hi, 

I have just added some information, concerning layout.

Also we have just committed the budget.

Target Market(s)

Mostly kids between 8 and 15 years.

Industry/Entity Type

It Company

Requirements
Must have
• We already have some characters, like Mr Wimble at the home page and our rabbits. We want to keep all of them, so new design have to match with there style (carton).

If you create an account, you will see we have a big nav bar with 6 tabs, and a little top bar. We absolutely need them to keep a easy navigation in website.

We also need some proposition of element style, like h1, h2, h3, hr, inputs, buttons, notification bubble, etc... So we can work to improve all our pages.
Nice to have
• I think the actual website is a little to wide (about 1000px width). Maybe something like 900px - 850px is more elegant ?
In this case, we can arrange pages to deal with it.

It can be cool if major colors are stil blue and green, to match a little with actual colors. But it's no very important.
Should not have
• We don't want too big header picture (for the all pages layout). I mean, players have to focus on the content.

We don't want photo realistic style, our style is cartoon.

We don't want flash. But Js animations are ok.

```html
<!DOCTYPE html>
<html lang="en">
<head>
<meta charset="utf-8">
<title>Quintamble – Racing and breeding game</title>
<link href="https://fonts.googleapis.com/css2?family=PT+Sans+Narrow:wght@400;700&family=Signika:wght@400;600&display=swap" rel="stylesheet">
<style>
:root{
  --red:#b5000a;
  --red-dark:#8e0008;
  --grass:#7fb13a;
  --nav-green:#8cc63f;
  --yellow:#ffe100;
  --orange:#ffb300;
  --blue-top:#5a97e3;
  --blue-bottom:#2c63c4;
  --white:#ffffff;
  --heading-green:#7aa832;
  --heading-red:#a8000c;
  --label-red:#d3101a;
  --tab-grey:#777;
  --tab-blue:#2a5db8;
  --text-grey:#777;
  --button:#7aa51f;
  --help:#3d6cc8;
}
*{box-sizing:border-box;margin:0;padding:0}
html,body{width:1200px;height:892px;overflow:hidden}
body{position:relative;font-family:"PT Sans Narrow",Arial,sans-serif;background:#c9a890}
.scenery{position:absolute;inset:0;background:linear-gradient(180deg,#d8c7b8 0%,#b99a8e 30%,#8a6f74 48%,#6a5a6a 60%,#a8915a 78%,#d8b046 100%)}
.topbar{position:absolute;left:0;top:0;width:1200px;height:98px;background:radial-gradient(ellipse at 50% 40%,#c6000c,var(--red) 60%,var(--red-dark));border-bottom:5px solid var(--grass)}
.mascot{position:absolute;border-radius:40%;background:linear-gradient(#e8e3c8,#b9b08a)}
.mascot.head{left:174px;top:6px;width:104px;height:90px}
.brand{position:absolute;left:308px;top:38px;font-family:"Signika",sans-serif;font-weight:600;font-size:27px;letter-spacing:2px;color:#ffc400}
.mainnav{position:absolute;left:651px;top:0;display:flex;font-family:"Signika",sans-serif;font-weight:600;font-size:13px;color:var(--white)}
.mainnav a{display:block;padding:0 12px;height:32px;line-height:34px;text-decoration:none;color:inherit}
.mainnav a.current{background:linear-gradient(#a6d860,var(--nav-green));border-radius:0 0 6px 6px;padding:0 13px}
.account{position:absolute;left:918px;top:0;width:112px;height:32px;background:linear-gradient(#ffd11a,#ffb400);border-radius:0 0 6px 6px;font-family:"Signika",sans-serif;font-size:12px;font-weight:600;color:#6a3a00;text-align:center;line-height:36px}
.panel{position:absolute;left:174px;top:129px;width:849px;height:619px;background:linear-gradient(var(--yellow) 10%,var(--orange));border-radius:4px;overflow:hidden}
.panel-title{height:49px;background:linear-gradient(var(--blue-top),var(--blue-bottom));color:var(--white);font-size:17px;font-weight:400;text-align:center;line-height:52px;letter-spacing:.3px}
.card{position:absolute;background:var(--white);border-radius:3px}
.h-green{color:var(--heading-green);font-size:18px;letter-spacing:.3px}
.step{font-size:11px;color:#666}
.step b{font-weight:400;color:var(--label-red)}
.field{position:absolute;height:21px;border:1px solid #ccc;border-radius:2px;background:#fff;box-shadow:inset 0 1px 2px #ddd}
.btn{position:absolute;background:linear-gradient(#93c02f,var(--button));color:#fff;font-size:11px;font-weight:700;text-align:center;line-height:18px;height:18px;border-radius:1px}
.h-red{position:absolute;color:var(--heading-red);font-size:17px;font-weight:400;letter-spacing:.3px}
.choices{position:absolute;left:110px;top:90px;font-family:"Signika",sans-serif;font-size:10.5px;color:#666;font-weight:600}
.choices div{display:flex;align-items:center;justify-content:space-between;width:80px;height:17px}
.choices svg{width:9px;height:9px}
.art{position:absolute;border-radius:4px}
.footer{position:absolute;left:0;top:790px;width:1200px;height:102px;background:var(--red);border-top:4px solid #c9b24b}
.footer .partners{position:absolute;left:176px;top:40px;font-size:11px;color:#f3b4b4;letter-spacing:.4px}
.badge{position:absolute;left:243px;top:33px;width:74px;height:26px;background:#1f57a8;border:1px solid #0a2a60}
.footer .links{position:absolute;right:170px;top:33px;font-size:10px;line-height:17px;color:#f3b4b4;text-align:right;letter-spacing:.3px}
</style>
</head>
<body>
<div class="scenery" role="img" aria-label="Soft sunset sky over hills and a golden field"></div>

<header class="topbar">
  <div class="mascot head" role="img" aria-label="Cartoon rabbit mascot lying on the grass"></div>
  <div class="brand">QUINTAMBLE</div>
  <nav class="mainnav">
    <a class="current" href="#">HOME</a><a href="#">NEWS</a><a href="#">FORUM</a><a href="#">RECORDS</a>
  </nav>
  <div class="account">Login &nbsp;|&nbsp; Sign Up</div>
</header>

<main class="panel">
  <h1 class="panel-title">THE COOLEST RACING AND BREEDING GAME THERE IS</h1>

  <section class="card" style="left:17px;top:78px;width:394px;height:158px">
    <div class="h-green" style="position:absolute;left:15px;top:18px">NEW PLAYER</div>
    <div class="step" style="position:absolute;left:15px;top:52px">1 - <b>CHOOSE YOUR BUNNY</b></div>
    <div class="art" style="left:16px;top:72px;width:60px;height:80px;background:linear-gradient(#eeeadb,#c9c2a3)" role="img" aria-label="Preview of the chosen rabbit"></div>
    <div class="choices">
      <div><svg viewBox="0 0 10 10"><circle cx="5" cy="5" r="5" fill="#d3101a"/><path d="M6 2.5 3.5 5 6 7.5" stroke="#fff" stroke-width="1.5" fill="none"/></svg>Original<svg viewBox="0 0 10 10"><circle cx="5" cy="5" r="5" fill="#d3101a"/><path d="M4 2.5 6.5 5 4 7.5" stroke="#fff" stroke-width="1.5" fill="none"/></svg></div>
      <div><svg viewBox="0 0 10 10"><circle cx="5" cy="5" r="5" fill="#d3101a"/><path d="M6 2.5 3.5 5 6 7.5" stroke="#fff" stroke-width="1.5" fill="none"/></svg>Gray<svg viewBox="0 0 10 10"><circle cx="5" cy="5" r="5" fill="#d3101a"/><path d="M4 2.5 6.5 5 4 7.5" stroke="#fff" stroke-width="1.5" fill="none"/></svg></div>
      <div><svg viewBox="0 0 10 10"><circle cx="5" cy="5" r="5" fill="#d3101a"/><path d="M6 2.5 3.5 5 6 7.5" stroke="#fff" stroke-width="1.5" fill="none"/></svg>Male<svg viewBox="0 0 10 10"><circle cx="5" cy="5" r="5" fill="#d3101a"/><path d="M4 2.5 6.5 5 4 7.5" stroke="#fff" stroke-width="1.5" fill="none"/></svg></div>
    </div>
    <div style="position:absolute;left:196px;top:16px;width:1px;height:124px;background:#ddd"></div>
    <div style="position:absolute;left:209px;top:19px;font-size:9.5px;color:var(--heading-green)">REGISTER IN JUST A COUPLE OF SECOND!</div>
    <div class="step" style="position:absolute;left:209px;top:44px">2 - <b>CHOOSE A USERNAME</b></div>
    <div class="field" style="left:209px;top:66px;width:172px"></div>
    <div class="step" style="position:absolute;left:209px;top:98px">3 - <b>OK! WE'RE GOOD TO GO!</b></div>
    <div class="btn" style="left:210px;top:121px;width:52px">PLAY</div>
  </section>

  <section class="card" style="left:429px;top:78px;width:402px;height:158px">
    <div class="art" style="left:10px;top:18px;width:104px;height:130px;background:linear-gradient(#9bc34a,#5a7e2a)" role="img" aria-label="Mr Wimble, the turtle race official"></div>
    <div class="h-green" style="position:absolute;left:127px;top:18px">CONNEXION</div>
    <div class="step" style="position:absolute;left:127px;top:44px"><b>USERNAME</b></div>
    <div class="step" style="position:absolute;left:250px;top:44px"><b>PASSWORD</b></div>
    <div class="field" style="left:127px;top:60px;width:112px"></div>
    <div class="field" style="left:250px;top:60px;width:112px"></div>
    <div style="position:absolute;left:375px;top:61px;width:18px;height:19px;background:var(--help);border-radius:2px;color:#fff;font-size:13px;text-align:center;line-height:19px">?</div>
    <div class="btn" style="left:128px;top:94px;width:52px">PLAY</div>
    <div style="position:absolute;left:188px;top:95px;font-size:11px;font-style:italic;color:var(--text-grey)">Forgotten your password?</div>
  </section>

  <div style="position:absolute;left:17px;top:265px;width:814px;height:1px;background:#f0c400"></div>

  <h2 class="h-red" style="left:17px;top:290px">GAME OVERVIEW</h2>
  <h2 class="h-red" style="left:428px;top:290px">TAKE PART IN RACES WITH OTHER PLAYERS</h2>

  <section class="card" style="left:17px;top:315px;width:394px;height:268px">
    <div style="position:absolute;left:43px;top:15px;display:flex;font-size:11px;color:var(--tab-grey);letter-spacing:.2px">
      <span style="padding:4px 9px">YOUR PEN</span>
      <span style="padding:4px 9px">YOUR ALLOTMENT</span>
      <span style="padding:4px 10px;background:#eef0f2;color:var(--tab-blue);border-radius:3px 3px 0 0">PROFESSIONS</span>
      <span style="padding:4px 9px">UNIVERSE</span>
    </div>
    <div class="art" style="left:8px;top:34px;width:377px;height:192px;background:radial-gradient(ellipse at 50% 40%,#ffffff,#dcdcdc)" role="img" aria-label="Alchemist and blacksmith characters at work"></div>
    <p style="position:absolute;left:12px;top:232px;width:370px;font-family:Arial,sans-serif;font-size:10.5px;line-height:12px;color:var(--text-grey)">Blacksmith, Alchemist, Gardner or Scientist! Progress in a profession and learn how to make really powerful objects!</p>
  </section>

  <section class="card" style="left:429px;top:315px;width:402px;height:268px">
    <div class="art" style="left:9px;top:9px;width:385px;height:251px;background:linear-gradient(#2c241c,#332a22 45%,#211a14)" role="img" aria-label="Live race preview with rabbits running on the track"></div>
  </section>
</main>

<footer class="footer">
  <div class="partners">PARTNERS:</div>
  <div class="badge" role="img" aria-label="Partner listing badge"></div>
  <div class="links">RULES - GENERAL TERMS AND CONDITIONS - CONTACT - QUINTAMBLE.COM 3.0<br>COPYRIGHT © 2012 QUINTAMBLE</div>
</footer>
</body>
</html>
```